Business Cards Needed for Innovative Healthcare Marketing Company

We are a marketing company focused on healthcare. Our company is all about rebranding yourself renewing your image and generating results. The phoenix stands for "reborn" or "rising" which we provide new brands for our clients we take their old brands and renew it with creativity and innovation. I am looking for a business card with color dimension. I have attached an example of a card I think has the look and feel of what I am trying to accomplish. I like that the card example has black and grey font colors, I like the font placement and the small logo, I really like the use of the colors on the right those are the colors of my logo. My logo is phoenix so maybe incorporating flames similar to that design. I would like the back a solid color maybe red with an opaque version of the logo and website. As a marketing company I am always open to creative liberty!

Target Market(s)

Doctors and business professionals.

Industry/Entity Type

Marketing

Contact Information for Business Card

Valcorne Health Care Marketing
Marla Tenwick- CEO
#(512)638-2974
email-marla@valcorne.com
website- valcorne.com

Font styles to use
Sans Serif

Colors
ec1f27
f37122
ffc214
fbed22
fbf289
f04a50

Requirements
Must have
• The logo and required information
Nice to have
• icons by the information
Should not have
• child like font

```html
<!DOCTYPE html>
<html lang="en">
<head>
<meta charset="utf-8">
<title>Valcorne Health Care Marketing – Business Cards</title>
<link rel="stylesheet" href="https://fonts.googleapis.com/css2?family=Raleway:wght@200;300&family=Roboto+Slab:wght@400;700&display=swap">
<style>
  :root {
    --stage: #3a2a22;
    --maroon-deep: #3e0b10;
    --maroon: #5e1219;
    --maroon-glow: #7a1a22;
    --yellow: #ffcc00;
    --flame: #f37122;
    --flame-red: #c73a2a;
    --ink: #2a1a12;
    --slate: #5a6b8a;
    --paper-white: #f4eeee;
    --mist: #b9b1b3;
    --rose: #d8484e;
  }
  html, body {
    margin: 0;
    padding: 0;
    width: 1200px;
    height: 913px;
    overflow: hidden;
    background: var(--stage);
  }
  .canvas {
    position: relative;
    width: 1200px;
    height: 913px;
  }
  .card {
    position: absolute;
    width: 520px;
    height: 300px;
    border-radius: 4px;
    overflow: hidden;
    box-shadow: 0 18px 40px rgba(0,0,0,0.45);
  }

  /* Back card */
  .card-back {
    left: 90px;
    top: 110px;
    background: radial-gradient(ellipse at 60% 30%, var(--maroon-glow) 0%, var(--maroon) 45%, var(--maroon-deep) 100%);
  }
  .back-brand {
    position: absolute;
    left: 230px;
    top: 82px;
    width: 260px;
  }
  .back-wordmark {
    font-family: "Raleway", sans-serif;
    font-weight: 200;
    font-size: 46px;
    letter-spacing: 2px;
    color: var(--paper-white);
    line-height: 1;
    padding-bottom: 6px;
    border-bottom: 1px solid rgba(244,238,238,0.55);
  }
  .back-tagline {
    font-family: "Raleway", sans-serif;
    font-weight: 300;
    font-size: 13px;
    letter-spacing: 1.5px;
    color: var(--paper-white);
    margin-top: 6px;
  }
  .back-website {
    font-family: "Roboto Slab", serif;
    font-size: 19px;
    color: var(--mist);
    margin-top: 26px;
    text-align: right;
  }
  .back-website .domain { color: var(--rose); }

  /* Front card */
  .card-front {
    left: 590px;
    top: 480px;
    background: var(--yellow);
  }
  .front-shape {
    position: absolute;
    inset: 0;
  }
  .front-brand {
    position: absolute;
    left: 40px;
    top: 150px;
    width: 210px;
    text-align: center;
  }
  .front-wordmark {
    font-family: "Raleway", sans-serif;
    font-weight: 300;
    font-size: 34px;
    letter-spacing: 1.5px;
    color: var(--flame-red);
    line-height: 1;
  }
  .front-tagline {
    font-family: "Raleway", sans-serif;
    font-weight: 300;
    font-size: 8px;
    letter-spacing: 1.2px;
    color: var(--flame-red);
    margin-top: 5px;
    border-top: 1px solid var(--flame-red);
    padding-top: 4px;
  }
  .contact-block {
    position: absolute;
    left: 330px;
    top: 62px;
    font-family: "Roboto Slab", serif;
  }
  .person-name {
    font-size: 22px;
    color: var(--slate);
    margin: 0;
    line-height: 1.1;
  }
  .person-name .surname {
    font-weight: 700;
    color: var(--ink);
    letter-spacing: 0.5px;
  }
  .person-role {
    font-size: 15px;
    color: var(--slate);
    margin: 2px 0 18px;
  }
  .contact-line {
    display: flex;
    align-items: center;
    gap: 8px;
    font-size: 14px;
    color: var(--ink);
    margin-bottom: 6px;
  }
  .contact-icon {
    width: 18px;
    height: 18px;
    flex: none;
  }
</style>
</head>
<body>
<main class="canvas">

  <section class="card card-back" aria-label="Card back">
    <div class="back-brand">
      <div class="back-wordmark">VALCORNE</div>
      <div class="back-tagline">HEALTHCARE MARKETING</div>
      <div class="back-website">www.<span class="domain">valcorne</span>.com</div>
    </div>
  </section>

  <section class="card card-front" aria-label="Card front">
    <svg class="front-shape" viewBox="0 0 520 300" preserveAspectRatio="none" aria-hidden="true">
      <defs>
        <radialGradient id="panel-glow" cx="35%" cy="40%" r="70%">
          <stop offset="0" stop-color="#6e1820"/>
          <stop offset="1" stop-color="#3e0b10"/>
        </radialGradient>
      </defs>
      <path d="M0 0 H232 Q300 130 292 300 H0 Z" fill="url(#panel-glow)"/>
      <path d="M256 0 H272 Q326 110 318 250 Q306 120 256 0 Z" fill="#5e1219"/>
    </svg>

    <div class="front-brand">
      <div class="front-wordmark">VALCORNE</div>
      <div class="front-tagline">HEALTHCARE MARKETING</div>
    </div>

    <div class="contact-block">
      <p class="person-name">Marla <span class="surname">TENWICK</span></p>
      <p class="person-role">CEO</p>
      <div class="contact-line">
        <svg class="contact-icon" viewBox="0 0 20 20" aria-hidden="true">
          <circle cx="10" cy="10" r="10" fill="#5e1219"/>
          <path d="M6.5 5.5 L8.5 5.2 L9.3 7.8 L8.1 8.7 Q9 11 11.3 11.9 L12.2 10.7 L14.8 11.5 L14.5 13.5 Q9.5 14 6.5 5.5 Z" fill="#ffcc00"/>
        </svg>
        <span>(512)638-2974</span>
      </div>
      <div class="contact-line">
        <svg class="contact-icon" viewBox="0 0 20 20" aria-hidden="true">
          <circle cx="10" cy="10" r="10" fill="#5e1219"/>
          <rect x="5" y="6.5" width="10" height="7" fill="#ffcc00"/>
          <path d="M5 6.5 L10 10.8 L15 6.5" fill="none" stroke="#5e1219" stroke-width="1"/>
        </svg>
        <span>marla@valcorne.com</span>
      </div>
    </div>
  </section>

</main>
</body>
</html>
```